Business Card Design Project : Ridgeline Press

In preparation for market launch, Tamarind's Ridgeline Press require the development of a business card. Ridgeline Press is a Community online publishing web portal. We provide the the city of Whistler located in B.C. (Canada) business directories, News, Classified ads, News, Events and blogs etc.

The main focus of the brand is to help local businesses to corporate with their online advertisement and marketing. Meeting our clients face to face is a must (B2B).

Target Market(s)

The target market is B2B customers. Business Owners to Marketing, advertising Managers

Industry/Entity Type

Business

Requirements
Must have
• - The business card will be two sided.
the BACK side will have our logo which consist of (icon, url,slogan) submited. The logo will be middle and centred.

The FRONT side should have company details:

Company Legal Name: TAMARIND RIDGELINE MEDIA

Owen Farsk
Director of Sales & Marketing

www.tamarindridgeline.biz
owen@tamarindridgeline.biz

Phone: 604 317 8842
#2714 - 582 E. Halvern St.
Vancouver, B.C. V7K2R4 Canada
Nice to have
• - For the "FRONT" side of our business card. You can separate or re-arrange with our logo components (icon, logo,slogan). It does not have to be together.

Also our company legal name is rather long so arrange or organize the name in a way to make it shorter. Your experience and creativity will have to come in play.
Should not have
• should not have other colors beside logo color and black text (2 colors). Also nothing Three dimensional

```html
<!DOCTYPE html>
<html lang="en">
<head>
<meta charset="utf-8">
<title>Ridgeline Press – Business Card</title>
<link href="https://fonts.googleapis.com/css2?family=Open+Sans:wght@400;600;700;800&display=swap" rel="stylesheet">
<style>
  :root {
    --brand-blue: #2a7fc4;
    --ink: #1a1a1a;
    --band-black: #1c1c1c;
    --rule-grey: #8a8a8a;
    --paper: #ffffff;
    --stage: #e8e5e1;
  }
  * { box-sizing: border-box; margin: 0; padding: 0; }
  html, body {
    width: 1200px; height: 412px; overflow: hidden;
    background: var(--stage);
    font-family: "Open Sans", Arial, sans-serif;
  }
  .canvas { position: relative; width: 1200px; height: 412px; }
  .card {
    position: absolute; top: 64px; width: 498px; height: 285px;
    background: var(--paper);
    box-shadow: 0 2px 6px rgba(0,0,0,0.18);
    overflow: hidden;
  }
  .card--front { left: 74px; }
  .card--back { left: 629px; }

  .brand-name {
    position: absolute; color: var(--brand-blue); font-weight: 700;
    white-space: nowrap; text-align: center;
  }
  .brand-url {
    position: absolute; color: var(--ink); font-weight: 700;
    white-space: nowrap; text-align: center; letter-spacing: -0.2px;
  }
  .brand-slogan {
    position: absolute; color: var(--brand-blue); font-weight: 400;
    white-space: nowrap; text-align: center;
  }

  /* front */
  .card--front .brand-name { left: 20px; width: 240px; top: 96px; font-size: 22px; }
  .card--front .brand-url { left: 14px; width: 252px; top: 150px; font-size: 16.5px; }
  .card--front .brand-slogan { left: 14px; width: 252px; top: 170px; font-size: 14px; }

  .divider {
    position: absolute; left: 269px; top: 64px; width: 1px; height: 140px;
    background: var(--rule-grey);
  }
  .contact { position: absolute; left: 288px; top: 70px; color: #333; font-size: 12.2px; line-height: 16.5px; }
  .contact__name { color: var(--brand-blue); font-weight: 700; font-size: 15px; line-height: 20px; }
  .contact__title { color: var(--brand-blue); margin-bottom: 11px; }
  .contact__line { display: flex; align-items: center; gap: 4px; }
  .contact__line svg { width: 10px; height: 10px; flex: none; }
  .contact__address { margin-top: 13px; }

  .footer-band { position: absolute; left: 0; bottom: 0; width: 498px; height: 24px; }
  .footer-band__label {
    position: absolute; right: 9px; bottom: 4px;
    color: #fff; font-weight: 700; font-size: 11.5px; letter-spacing: 1.6px;
  }

  /* back */
  .card--back .brand-name { left: 0; width: 498px; top: 96px; font-size: 30px; }
  .card--back .brand-url { left: 0; width: 498px; top: 161px; font-size: 24px; }
  .card--back .brand-slogan { left: 0; width: 498px; top: 190px; font-size: 18.5px; }
</style>
</head>
<body>
<main class="canvas">

  <section class="card card--front" aria-label="Business card front">
    <div class="brand-name">Ridgeline Press</div>
    <div class="brand-url">www.tamarindridgeline.biz</div>
    <div class="brand-slogan">Your information gateway</div>

    <div class="divider"></div>

    <div class="contact">
      <div class="contact__name">Owen Farsk</div>
      <div class="contact__title">Director of Sales &amp; Marketing</div>
      <div class="contact__line">
        <svg viewBox="0 0 10 10" aria-hidden="true"><path d="M2.2 0.8 L3.6 2.8 L2.7 3.8 C3.3 5.1 4.8 6.6 6.1 7.2 L7.1 6.3 L9.1 7.7 L8.3 9.2 C4.6 9.2 0.8 5.4 0.8 1.6 Z" fill="none" stroke="#333" stroke-width="0.9"/></svg>
        <span>604 317 8842</span>
      </div>
      <div class="contact__line">
        <svg viewBox="0 0 10 10" aria-hidden="true"><rect x="0.8" y="2.2" width="8.4" height="6" fill="#333"/><path d="M0.8 2.2 L5 5.6 L9.2 2.2" fill="none" stroke="#fff" stroke-width="0.9"/></svg>
        <span>owen@tamarindridgeline.biz</span>
      </div>
      <div class="contact__address">
        #2714 - 582 E. Halvern St.<br>
        Vancouver, B.C. V7K2R4 Canada
      </div>
    </div>

    <div class="footer-band">
      <svg width="498" height="24" viewBox="0 0 498 24" aria-hidden="true">
        <polygon points="0,3 256,3 240,24 0,24" fill="var(--brand-blue)"/>
        <polygon points="266,0 498,0 498,24 246,24" fill="var(--band-black)"/>
      </svg>
      <span class="footer-band__label">TAMARIND RIDGELINE MEDIA</span>
    </div>
  </section>

  <section class="card card--back" aria-label="Business card back">
    <div class="brand-name">Ridgeline Press</div>
    <div class="brand-url">www.tamarindridgeline.biz</div>
    <div class="brand-slogan">Your information gateway</div>
  </section>

</main>
</body>
</html>
```